Harlow Mechanical Contractors needs a Website

Create basic website for commercial plumbing and mechanical contractor; to include pictures of works in progress and completed works, description of all services offered and geographical locations and licenses

Target Market(s)

General Contractors, Real Estate Developers, Construction Companies

Industry/Entity Type

Construction

Coding

Coded - Design and coding required

Number of Pages Required

5+ page

• See logo attached to project

Colors
0392cd

```html
<!DOCTYPE html>
<html lang="en">
<head>
<meta charset="utf-8">
<title>Harlow Mechanical Contractors</title>
<link rel="stylesheet" href="https://fonts.googleapis.com/css2?family=Raleway:wght@400;500;600;700&family=Open+Sans:ital,wght@0,400;0,600;1,400&display=swap">
<style>
:root{
  --brand:#0392cd;
  --brand-dark:#1d3f5e;
  --ink:#3a3a3a;
  --muted:#8a8a8a;
  --nav:#6a6a6a;
  --light:#f0f0f0;
  --card-cap:#e6e6e6;
  --footer:#6b6b6b;
  --footer-base:#5b5b5b;
  --social:#3b3b3b;
  --white:#ffffff;
}
*{margin:0;padding:0;box-sizing:border-box}
html,body{width:1200px;height:2362px;overflow:hidden;background:var(--white)}
body{position:relative;font-family:"Open Sans",Arial,sans-serif;color:var(--ink)}
h1,h2,h3,h4{font-weight:400}

/* header */
.site-header{position:absolute;left:0;top:0;width:1200px;height:101px;background:var(--white);z-index:3}
.brand{position:absolute;left:120px;top:10px;display:flex;align-items:center;gap:16px}
.brand-mark{width:80px;height:80px;border-radius:50%;background:var(--brand);flex:none}
.brand-name{font-family:"Raleway",Arial,sans-serif;font-weight:700;font-size:17px;line-height:18px;color:var(--brand-dark);text-transform:uppercase}
.main-nav{position:absolute;top:42px;left:428px;font-family:"Raleway",Arial,sans-serif;font-size:15px;text-transform:uppercase;color:var(--nav)}
.main-nav span{position:absolute;white-space:nowrap;top:0}
.main-nav .active{color:var(--brand-dark);font-weight:500}
.header-phone{position:absolute;left:944px;top:38px;display:flex;align-items:center;gap:8px;font-size:18px;color:var(--ink)}

/* hero */
.hero{position:absolute;left:0;top:101px;width:1200px;height:475px;background:linear-gradient(100deg,#8d9296 0%,#b7bbbe 30%,#a5a9ac 55%,#6e7277 80%,#4c5056 100%)}
.hero-title{position:absolute;left:0;width:1200px;top:168px;text-align:center;color:var(--white);font-family:"Raleway",Arial,sans-serif;text-transform:uppercase}
.hero-title .line1{display:block;font-size:35px;font-weight:500;line-height:44px;padding-right:10px}
.hero-title .line2{display:block;font-size:41px;font-weight:600;line-height:50px}
.slider-dots{position:absolute;display:flex;gap:5px}
.slider-dots i{display:block;width:15px;height:15px;border-radius:50%;background:var(--white);border:2px solid var(--white)}
.slider-dots i.off{background:transparent}

/* welcome */
.welcome{position:absolute;left:0;top:576px;width:1200px;height:388px;background:var(--white)}
.welcome-photo{position:absolute;left:0;top:0;width:598px;height:388px;background:linear-gradient(90deg,#cfd3d6 0%,#e6e8ea 45%,#f7f7f7 80%,#ffffff 100%)}
.welcome-kicker{position:absolute;left:564px;top:78px;font-family:"Raleway",Arial,sans-serif;font-size:22px;color:#333;text-transform:uppercase}
.welcome-title{position:absolute;left:564px;top:107px;font-family:"Raleway",Arial,sans-serif;font-weight:400;font-size:28px;color:#333;text-transform:uppercase}
.welcome-text{position:absolute;left:564px;top:152px;width:510px;font-size:12.6px;line-height:25px;color:var(--muted)}
.btn-outline{position:absolute;left:564px;top:274px;width:126px;height:38px;border:2px solid var(--brand-dark);color:var(--brand-dark);font-family:"Raleway",Arial,sans-serif;font-weight:700;font-size:13px;display:flex;align-items:center;justify-content:center}

/* services */
.services{position:absolute;left:0;top:964px;width:1200px;height:365px;background:linear-gradient(180deg,#0a8fcb 0%,#0a84c2 100%);color:var(--white)}
.section-title-light{position:absolute;left:0;width:1200px;top:32px;text-align:center;font-family:"Raleway",Arial,sans-serif;font-weight:400;font-size:26px;text-transform:uppercase}
.title-rule{position:absolute;left:476px;top:76px;width:256px;height:1px;background:rgba(255,255,255,.8)}
.service{position:absolute;top:134px;width:290px;text-align:center}
.service svg{display:block;margin:0 auto}
.service h3{font-family:"Raleway",Arial,sans-serif;font-weight:500;font-size:19px;margin-top:16px}
.service p{font-size:13px;line-height:20px;margin-top:2px;color:rgba(255,255,255,.9)}

/* projects */
.projects-title{position:absolute;left:113px;top:1348px;font-family:"Raleway",Arial,sans-serif;font-weight:400;font-size:24px;color:var(--brand);text-transform:uppercase}
.project-card{position:absolute;top:1419px;width:237px;height:224px;border-bottom:4px solid var(--brand);background:var(--card-cap)}
.project-photo{height:132px}
.project-card .cap{font-family:"Raleway",Arial,sans-serif;font-size:15px;color:#444;text-transform:uppercase;padding:27px 0 0 22px}
.project-card.featured{background:var(--brand)}
.project-card.featured .cap{color:var(--white);padding:18px 0 0 24px;font-weight:500}
.project-card.featured .sub{color:rgba(255,255,255,.9);font-size:11px;line-height:15px;padding:4px 20px 0 24px}
.divider{position:absolute;left:0;top:1701px;width:1200px;height:2px;background:#dcdcdc}

/* testimonials */
.testimonials{position:absolute;left:0;top:1703px;width:1200px;height:349px;background:var(--light)}
.testimonials h2{position:absolute;left:0;width:1200px;top:44px;text-align:center;font-family:"Raleway",Arial,sans-serif;font-size:24px;color:#4a4a4a}
.avatar{position:absolute;left:274px;top:97px;width:88px;height:88px;border-radius:50%;background:linear-gradient(160deg,#c9ced3,#8e99a4);border:3px solid var(--white)}
.author{position:absolute;left:230px;width:176px;text-align:center;font-size:14px;color:#555}
.author.loc{font-size:12px;color:#666}
.quote-rule{position:absolute;left:404px;top:89px;width:1px;height:126px;background:#bdbdbd}
.quote{position:absolute;left:460px;top:118px;width:580px;font-style:italic;font-size:16px;line-height:28px;color:#666}
.qmark{position:absolute;font-family:Georgia,serif;font-size:54px;color:#aaa;line-height:1}

/* footer */
.site-footer{position:absolute;left:0;top:2052px;width:1200px;height:255px;background:var(--footer);color:var(--white)}
.footer-brand{position:absolute;left:112px;top:50px;display:flex;align-items:center;gap:16px}
.footer-brand .mark{width:80px;height:80px;border-radius:50%;background:var(--white);flex:none}
.footer-brand .name{font-family:"Raleway",Arial,sans-serif;font-weight:700;font-size:17px;line-height:18px;color:var(--white);text-transform:uppercase}
.footer-col{position:absolute;top:56px}
.footer-col h4{font-family:"Raleway",Arial,sans-serif;font-size:18px;text-transform:uppercase;margin-bottom:12px}
.footer-col li{list-style:none;font-size:13px;line-height:24.5px}
.footer-col.contact li{font-size:12px}
.footer-col li svg{vertical-align:-2px;margin-right:5px}
.social{position:absolute;top:89px;display:flex;gap:10px}
.social span{width:38px;height:38px;border-radius:50%;background:var(--social);display:flex;align-items:center;justify-content:center}
.footer-base{position:absolute;left:0;top:2307px;width:1200px;height:55px;background:var(--footer-base);color:#b5b5b5;font-size:12px;text-align:center;line-height:55px;padding-right:60px}
</style>
</head>
<body>

<header class="site-header">
  <div class="brand">
    <div class="brand-mark"></div>
    <div class="brand-name">Harlow<br>Mechanical<br>Contractors</div>
  </div>
  <nav class="main-nav">
    <span class="active" style="left:0">Home</span>
    <span style="left:81px">About Us</span>
    <span style="left:191px">Services</span>
    <span style="left:298px">Project</span>
    <span style="left:397px">Contact Us</span>
  </nav>
  <div class="header-phone">
    <svg width="18" height="18" viewBox="0 0 24 24"><path fill="#0392cd" d="M6.6 10.8a15.1 15.1 0 0 0 6.6 6.6l2.2-2.2c.3-.3.7-.4 1-.2 1.1.4 2.3.6 3.6.6.6 0 1 .4 1 1V20c0 .6-.4 1-1 1A17 17 0 0 1 3 4c0-.6.4-1 1-1h3.5c.6 0 1 .4 1 1 0 1.3.2 2.5.6 3.6.1.3 0 .7-.2 1z"/></svg>
    <span>555-214-7730</span>
  </div>
</header>

<section class="hero" role="img" aria-label="Plumbing contractor in a hard hat checking a clipboard beside pipework, gauges and valves">
  <h1 class="hero-title"><span class="line1">Expertise Plumbing</span><span class="line2">Services &amp; Contractors</span></h1>
  <div class="slider-dots" style="left:559px;top:441px"><i class="off"></i><i></i><i></i><i></i></div>
</section>

<section class="welcome">
  <div class="welcome-photo" role="img" aria-label="Plumber in a yellow hard hat and plaid shirt reading a plan"></div>
  <p class="welcome-kicker">Welcome to Harlow</p>
  <h2 class="welcome-title">Mechanical Contractors</h2>
  <p class="welcome-text">Cras a ante vitae enim iaculis aliquam Mauris nunc quam venenatis nec euismod sit amet egestas placerat est Pellentesque habitant morbi tristique senectus et netus et malesuada fames ac turpis egestas Cras id elit Integer quis urna Ut ante enim dapibus malesuada fringilla eu condimentum quis tellus</p>
  <a class="btn-outline">READ MORE</a>
</section>

<section class="services">
  <h2 class="section-title-light">Services Provides</h2>
  <div class="title-rule"></div>

  <div class="service" style="left:145px">
    <svg width="76" height="68" viewBox="0 0 76 68" fill="#fff">
      <rect x="20" y="4" width="22" height="5" rx="2"/>
      <rect x="28" y="8" width="6" height="10"/>
      <rect x="8" y="18" width="52" height="14" rx="3"/>
      <rect x="60" y="16" width="8" height="18" rx="2"/>
      <rect x="8" y="32" width="14" height="12"/>
      <path d="M10 48h10l-2 16h-6z"/>
    </svg>
    <h3>Full Plumbing Install</h3>
    <p>malesuada fames ac turpis egestas Cras id elit Integer quis urna Ut ante enim dapibus malesuada fringilla</p>
  </div>

  <div class="service" style="left:466px">
    <svg width="76" height="68" viewBox="0 0 76 68" fill="#fff">
      <path d="M14 66V34a24 24 0 0 1 48 0v32h-12V34a12 12 0 0 0-24 0v32z"/>
      <circle cx="38" cy="12" r="10"/>
      <rect x="36" y="2" width="4" height="20" fill="#0a8fcb"/>
      <rect x="28" y="10" width="20" height="4" fill="#0a8fcb"/>
      <rect x="10" y="42" width="20" height="5"/>
      <rect x="46" y="42" width="20" height="5"/>
    </svg>
    <h3>Building Plumbing</h3>
    <p>malesuada fames ac turpis egestas Cras id elit Integer quis urna Ut ante enim dapibus malesuada</p>
  </div>

  <div class="service" style="left:779px">
    <svg width="80" height="68" viewBox="0 0 80 68" fill="#fff">
      <rect x="28" y="6" width="24" height="5" rx="2"/>
      <rect x="37" y="10" width="6" height="10"/>
      <path d="M6 66V34a10 10 0 0 1 10-10h48a10 10 0 0 1 10 10v32h-10V36H16v30z"/>
    </svg>
    <h3>Repair &amp; Leakage</h3>
    <p>malesuada fames ac turpis egestas Cras id elit Integer quis urna Ut ante enim dapibus malesuada fringilla</p>
  </div>
</section>

<h2 class="projects-title">Our Projects</h2>

<article class="project-card" style="left:115px">
  <div class="project-photo" role="img" aria-label="Blue and red pipework in a plant room" style="background:linear-gradient(135deg,#9aa3ab,#3c6fa8 60%,#b34a48)"></div>
  <p class="cap">Building Tittle Here</p>
</article>
<article class="project-card featured" style="left:362px">
  <div class="project-photo" role="img" aria-label="Washroom with a row of basins and yellow walls" style="background:linear-gradient(180deg,#b8892e,#d9b25c 55%,#8d8f90)"></div>
  <p class="cap">Building Tittle Here</p>
  <p class="sub">Aliquam erat volutpat Quisque dignissim congue leo</p>
</article>
<article class="project-card" style="left:608px">
  <div class="project-photo" role="img" aria-label="Long washroom vanity with mirrors" style="background:linear-gradient(180deg,#cfd4d6,#eef0f1 50%,#9b8f86)"></div>
  <p class="cap">Building Tittle Here</p>
</article>
<article class="project-card" style="left:854px">
  <div class="project-photo" role="img" aria-label="Tiled toilet cubicle" style="background:linear-gradient(180deg,#c7d3e6,#e8edf4 60%,#8d9196)"></div>
  <p class="cap">Building Tittle Here</p>
</article>

<div class="divider"></div>

<section class="testimonials">
  <h2>TESTIMONIALS</h2>
  <div class="avatar" role="img" aria-label="Portrait of the reviewer"></div>
  <p class="author" style="top:200px">By Author Name</p>
  <p class="author loc" style="top:225px">City Location</p>
  <div class="quote-rule"></div>
  <span class="qmark" style="left:428px;top:106px">&ldquo;</span>
  <p class="quote">Cum sociis natoque penatibus et magnis dis parturient montes nascetur ridiculus mus In iaculis facilisis massa Etiam eu urna Sed porta Suspendisse quam leo molestie sed luctus quis feugiat in pede</p>
  <span class="qmark" style="left:742px;top:184px">&rdquo;</span>
  <div class="slider-dots" style="left:572px;top:254px">
    <i class="off" style="border-color:#999;width:14px;height:14px"></i>
    <i style="background:#999;border-color:#999;width:14px;height:14px"></i>
    <i style="background:#999;border-color:#999;width:14px;height:14px"></i>
  </div>
</section>

<footer class="site-footer">
  <div class="footer-brand">
    <div class="mark"></div>
    <div class="name">Harlow<br>Mechanical<br>Contractors</div>
  </div>
  <div class="footer-col" style="left:393px">
    <h4>Company</h4>
    <ul><li>Home</li><li>About Us</li><li>Our Services</li><li>Case Studies</li></ul>
  </div>
  <div class="footer-col" style="left:531px">
    <h4>Resources</h4>
    <ul><li>Team</li><li>Support</li><li>Blogs</li><li>Contact Us</li></ul>
  </div>
  <div class="footer-col contact" style="left:689px">
    <h4>Contact Us</h4>
    <ul>
      <li>Company Name</li>
      <li>18 Kestrel Rd Northgate QLD 4013</li>
      <li><svg width="13" height="13" viewBox="0 0 24 24"><path fill="#fff" d="M6.6 10.8a15.1 15.1 0 0 0 6.6 6.6l2.2-2.2c.3-.3.7-.4 1-.2 1.1.4 2.3.6 3.6.6.6 0 1 .4 1 1V20c0 .6-.4 1-1 1A17 17 0 0 1 3 4c0-.6.4-1 1-1h3.5c.6 0 1 .4 1 1 0 1.3.2 2.5.6 3.6.1.3 0 .7-.2 1z"/></svg>(07) 5550 4127</li>
      <li><svg width="13" height="11" viewBox="0 0 24 18"><path fill="#fff" d="M0 0h24v18H0z"/><path d="M1 1l11 9 11-9" stroke="#6b6b6b" stroke-width="2" fill="none"/></svg>sales@harlowmech.com.au</li>
    </ul>
  </div>
  <div class="footer-col" style="left:909px">
    <h4>Follow Us</h4>
  </div>
  <div class="social" style="left:910px">
    <span aria-label="Website"><svg width="18" height="18" viewBox="0 0 24 24" fill="none" stroke="#fff" stroke-width="2"><circle cx="12" cy="12" r="9"/><path d="M3 12h18M12 3c3 3 3 15 0 18M12 3c-3 3-3 15 0 18"/></svg></span>
    <span aria-label="Chat"><svg width="18" height="18" viewBox="0 0 24 24" fill="#fff"><path d="M3 4h18v12H9l-5 4v-4H3z"/></svg></span>
    <span aria-label="Share"><svg width="18" height="18" viewBox="0 0 24 24" fill="#fff"><circle cx="18" cy="5" r="3"/><circle cx="6" cy="12" r="3"/><circle cx="18" cy="19" r="3"/><path d="M8 11l8-5M8 13l8 5" stroke="#fff" stroke-width="2"/></svg></span>
    <span aria-label="Newsletter"><svg width="18" height="16" viewBox="0 0 24 18"><path fill="#fff" d="M0 0h24v18H0z"/><path d="M1 1l11 9 11-9" stroke="#3b3b3b" stroke-width="2" fill="none"/></svg></span>
  </div>
</footer>

<div class="footer-base">&copy; 2016 Company Name &nbsp;All right reserved</div>

</body>
</html>
```